Commercial Cleaning Company Website Design

We are working with Harbor Tidy Team. They are a commercial cleaning company that needs a new website design.

Some sites to use for inspiration:

https://www.plenvask.com
https://gleam-panecare.com
https://tidwellhelpers.net
https://quietnesthouse.com
https://www.thedustingbureau.com
https://www.pennytidy.com

Thank you for taking the time to consider designing a website for us. We are web developers based in Stockton and Los Angeles, CA, USA. Most of our projects go through the same process. Understanding this process may help you win a project with us. We custom-code all of our websites in-house. We don’t have any requirements as to what tools you use for your design, but we prefer Figma files. For any design that we label as four-stars, we send it to the client for review. The client picks the final design they want us to use. Once we complete this process, we will continue to show additional clients all the four-star sites and purchase them later. Your designs will have multiple chances to sell. For better chances of success, we ask that you follow these guidelines.

IMAGES:
If you use any images or icons in the design, we ask that you have a link to the asset so we can purchase the image/icon. Most of the designs we submit do not have the customer’s images on them unless they have some great images. Be creative; show us the feeling you are trying to portray with your image choices. Use any royalty-free site you choose. We subscribe to Adobe and mainly use their images, but we can purchase images outside of Adobe.

PLEASE NOTE: we will not submit designs to clients with watermarks on the images.

FONTS:
We ask that you identify the fonts used in the design. This can be done in a message if you want. We typically use Google Fonts and Adobe Fonts.

CONTENT:
We're always open to different content and ideas. We often submit designs with stock images so the client can see our vision. We typically take pictures after the website launch to use their images with our vision. Lorem Ipsum is fine for paragraphs, but we ask that you write the headers in correct English. We want to be able to show the vision and identify the sections of the website.

INSPIRATION:
We typically add a couple of links in the brief of websites we like to help you get started in your design.

REVISIONS:
We do not often ask for revisions of the designs unless we see something in the design that may not appeal to the client. If there are slight changes that we want to make, we do that in the development process.

FEEDBACK:
We rarely give feedback on designs during the design process. We are working on many website projects and do not have the time to provide feedback. We usually respond if your request is well thought out and asks specific questions, but a note asking “feedback, please” usually goes unanswered.

```html
<!DOCTYPE html>
<html lang="en">
<head>
<meta charset="utf-8">
<title>Harbor Tidy Team – Professional Cleaning Services</title>
<link href="https://fonts.googleapis.com/css2?family=Poppins:wght@400;500;600;700&display=swap" rel="stylesheet">
<style>
:root{
  --blue:#2152c0;
  --blue-deep:#1a44a8;
  --red:#e8321e;
  --ink:#1d1d1d;
  --text:#3a3a3a;
  --grey-bg:#efefef;
  --white:#ffffff;
}
*{margin:0;padding:0;box-sizing:border-box}
html,body{width:1200px;height:4464px;overflow:hidden}
body{font-family:'Poppins',sans-serif;color:var(--text);background:var(--white);position:relative}
.abs{position:absolute}
.btn{position:absolute;display:flex;align-items:center;justify-content:center;border-radius:40px;font-weight:600;font-size:14px;text-transform:uppercase;letter-spacing:.2px}
.btn-red{background:var(--red);color:var(--white)}
.btn-blue{background:var(--blue);color:var(--white)}
.btn-outline{border:2px solid var(--red);color:var(--red);background:transparent}
.heading{position:absolute;font-weight:600;color:var(--blue);text-transform:uppercase;letter-spacing:-.5px}
.rule{position:absolute;height:3px;background:var(--red);border-radius:2px}

/* header */
.brand{position:absolute;left:70px;top:52px;display:flex;align-items:center;gap:12px}
.brand-dot{width:34px;height:34px;border-radius:50%;background:var(--red)}
.brand-name{font-weight:600;font-size:26px;color:var(--blue);letter-spacing:1px}
.nav{position:absolute;top:100px;right:62px;display:flex;gap:34px;font-size:13.5px;color:var(--ink);font-weight:500}
.nav .active{font-weight:700}

/* hero */
.hero{position:absolute;left:0;top:150px;width:1200px;height:603px;background:var(--grey-bg)}
.hero-photo{position:absolute;left:0;top:0;width:640px;height:603px;background:linear-gradient(90deg,#6f6a66 0%,#a9a49e 55%,#efefef 100%)}
.hero-title{position:absolute;left:532px;top:130px;color:var(--blue);font-weight:700;line-height:1;text-transform:uppercase}
.hero-title .l1{font-size:78px;display:block;letter-spacing:-1px}
.hero-title .l2{font-size:61px;display:block;letter-spacing:-.5px;margin-top:4px}
.hero-copy{position:absolute;left:535px;top:285px;width:560px;font-size:14px;line-height:26px;color:var(--text)}

/* about */
.about-lead{position:absolute;left:92px;top:1010px;width:500px;font-size:20px;line-height:31px;font-weight:600;color:var(--ink)}
.about-copy{position:absolute;left:92px;top:1084px;width:488px;font-size:13.5px;line-height:27.5px;text-align:justify}
.ring{position:absolute;border:2px solid var(--red);border-radius:50%}
.disc{position:absolute;border-radius:50%}

/* why */
.why{position:absolute;left:0;top:1488px;width:1200px;height:399px;background:linear-gradient(90deg,#2b5cc8,#3c6bd1 50%,#2a58c4)}
.why-card{position:absolute;top:1705px;width:251px;height:68px;background:var(--white);border-radius:34px;display:flex;align-items:center;padding-left:12px;gap:14px}
.why-icon{width:44px;height:44px;border-radius:50%;background:var(--red);flex:none;display:flex;align-items:center;justify-content:center}
.why-card h4{font-size:10.5px;font-weight:700;color:var(--ink);text-transform:uppercase}
.why-card p{font-size:8.5px;line-height:12px;color:var(--text);width:170px;margin-top:2px}

/* services */
.svc{position:absolute;top:2136px;width:347px;height:465px;background:var(--white);box-shadow:0 2px 14px rgba(0,0,0,.12)}
.svc-photo{position:absolute;left:18px;top:18px;width:311px;height:227px}
.svc h3{position:absolute;left:0;top:268px;width:100%;text-align:center;color:var(--red);font-size:18px;font-weight:500}
.svc p{position:absolute;left:20px;top:307px;width:307px;text-align:center;font-size:11px;line-height:19px}
.svc .btn{left:112px;top:396px;width:123px;height:45px;font-size:12px}

/* welcome */
.welcome{position:absolute;left:0;top:2813px;width:1200px;height:496px;background:linear-gradient(100deg,#e23a23,#ef4b33 50%,#e2371f)}
.welcome-kicker{position:absolute;left:0;top:2925px;width:1200px;text-align:center;color:var(--white);font-size:15px;font-weight:500}
.welcome-title{position:absolute;left:0;top:2963px;width:1200px;text-align:center;color:var(--white);font-size:68px;font-weight:600;letter-spacing:-.5px;text-transform:uppercase}
.welcome-copy{position:absolute;left:150px;top:3056px;width:900px;text-align:center;color:var(--white);font-size:13.5px;line-height:23px}

/* contact */
.contact-sub{position:absolute;left:77px;top:3510px;font-size:13.5px;color:var(--ink)}
.field{position:absolute;background:var(--white);box-shadow:0 1px 8px rgba(0,0,0,.14);font-size:14px;color:#a8a8a8;padding:16px 12px}

/* footer */
.footer{position:absolute;left:0;top:3985px;width:1200px;height:479px;background:linear-gradient(180deg,#2a5bc8,#2350b8)}
.foot-h{position:absolute;color:var(--white);font-size:24px;font-weight:500;text-transform:uppercase}
.foot-rule{position:absolute;height:2px;width:60px;background:var(--white)}
.foot-list{position:absolute;left:552px;top:4180px;list-style:none;color:var(--white);font-size:14px}
.foot-list li{height:32.5px;display:flex;align-items:center;gap:16px}
.foot-list li::before{content:"";width:7px;height:7px;border-radius:50%;background:var(--white)}
.foot-contact{position:absolute;left:826px;display:flex;align-items:center;gap:16px;color:var(--white);font-size:14px;line-height:22px}
.foot-icon{width:36px;height:36px;border-radius:50%;background:var(--white);flex:none;display:flex;align-items:center;justify-content:center}
.social{position:absolute;top:4240px;width:36px;height:36px;border-radius:50%;background:var(--white)}
.copyright{position:absolute;left:0;top:4408px;width:1200px;text-align:center;color:var(--white);font-size:15px}
</style>
</head>
<body>

<!-- header -->
<div class="brand"><span class="brand-dot"></span><span class="brand-name">HARBOR TIDY TEAM</span></div>
<div class="btn btn-outline" style="left:725px;top:32px;width:232px;height:42px;color:var(--ink);font-size:13px">Get Your Free Estimate</div>
<div class="btn btn-red" style="left:974px;top:32px;width:162px;height:42px;font-size:14px;gap:8px;justify-content:flex-start;padding-left:10px">
  <svg width="24" height="24" viewBox="0 0 24 24"><circle cx="12" cy="12" r="12" fill="#fff"/><path d="M8 6.5c.6-.4 1.3-.2 1.6.4l.9 1.8c.3.5.1 1.1-.3 1.4l-.8.6c.6 1.3 1.6 2.4 2.9 3.1l.6-.8c.3-.4.9-.6 1.4-.3l1.8.9c.6.3.8 1 .4 1.6l-.6 1c-.5.8-1.5 1.1-2.4.8-3-1.1-5.3-3.5-6.3-6.5-.3-.9 0-1.9.8-2.4z" fill="#e8321e"/></svg>
  555-201-4870</div>
<nav class="nav"><span class="active">HOME</span><span>ABOUT US</span><span>OUR SERVICES</span><span>OUR TESTIMONIALS</span><span>CONTACT US</span></nav>

<!-- hero -->
<section class="hero">
  <div class="hero-photo" role="img" aria-label="Cleaner in mask and gloves wiping a glass surface"></div>
  <h1 class="hero-title"><span class="l1">Professional</span><span class="l2">Cleaning Services</span></h1>
  <p class="hero-copy">Lorem ipsum dolor sit amet, consectetur adipiscing elit, sed do eiusmod tempor incididunt ut labore et dolore magna aliqua. Quis ipsum suspendisse</p>
  <div class="btn btn-red" style="left:533px;top:365px;width:236px;height:61px;font-size:15px">Book Now</div>
  <div class="btn btn-outline" style="left:789px;top:365px;width:238px;height:61px;font-size:15px">Call Us Today</div>
</section>

<!-- about -->
<h2 class="heading" style="left:91px;top:920px;font-size:48px">About Us</h2>
<div class="rule" style="left:92px;top:985px;width:64px"></div>
<p class="about-lead">Lorem ipsum dolor sit amet, consectetur, Ut enim adipiscing elit,sed do eiusmod tempor.</p>
<p class="about-copy">Sed ut perspiciatis unde omnis iste natus error sit voluptatem accusantium doloremque laudantium, totam rem aperiam, eaque ipsa quae ab illo inventore veritatis et quasi architecto beatae vitae dicta sunt explicabo. Nemo enim ipsam voluptatem quia voluptas sit aspernatur aut odit aut fugit, sed quia consequuntur magni dolores eos qui ratione voluptatem sequi nesciunt.</p>
<div class="btn btn-red" style="left:92px;top:1267px;width:155px;height:50px;font-size:13px">Read More</div>
<div class="ring" style="left:603px;top:870px;width:514px;height:514px"></div>
<div class="disc" role="img" aria-label="Cleaner holding a spray bottle and squeegee with tool belt" style="left:631px;top:898px;width:458px;height:458px;background:radial-gradient(circle at 50% 40%,#6b6257,#2c2a28 70%)"></div>

<!-- why choose us -->
<section class="why" role="img" aria-label="Blue-tinted background of gloved hands cleaning"></section>
<h2 class="heading" style="left:0;top:1560px;width:1200px;text-align:center;color:#fff;font-size:48px">Why Choose Us</h2>
<div class="rule" style="left:553px;top:1631px;width:94px;background:#fff"></div>
<div class="why-card" style="left:75px"><span class="why-icon"><svg width="26" height="20" viewBox="0 0 26 20" fill="none" stroke="#fff" stroke-width="1.6"><circle cx="7" cy="6" r="3"/><circle cx="13" cy="5" r="3.4"/><circle cx="19" cy="6" r="3"/><path d="M2 17c0-4 3-6 5-6M24 17c0-4-3-6-5-6M7 18c0-4 3-7 6-7s6 3 6 7"/></svg></span><div><h4>Professional Team</h4><p>Lorem ipsum dolor sit amet, consectetur adipiscing elit, sed do eiusmincidi</p></div></div>
<div class="why-card" style="left:344px"><span class="why-icon"><svg width="26" height="26" viewBox="0 0 26 26" fill="none" stroke="#fff" stroke-width="1.8"><circle cx="13" cy="13" r="10"/><path d="M13 7v6l4 3"/></svg></span><div><h4>On Time Service</h4><p>Lorem ipsum dolor sit amet, consectetur adipiscing elit, sed do eiusmod</p></div></div>
<div class="why-card" style="left:614px"><span class="why-icon"><svg width="26" height="26" viewBox="0 0 26 26" fill="none" stroke="#fff" stroke-width="1.8"><circle cx="13" cy="13" r="10"/><text x="13" y="18" text-anchor="middle" fill="#fff" stroke="none" font-family="Poppins,sans-serif" font-size="13" font-weight="600">$</text></svg></span><div><h4>Transparent Pricing</h4><p>Lorem ipsum dolor sit amet, consectetur adipiscing elit, sed</p></div></div>
<div class="why-card" style="left:883px"><span class="why-icon"><svg width="26" height="20" viewBox="0 0 26 20" fill="none" stroke="#fff" stroke-width="1.6"><circle cx="7" cy="6" r="3"/><circle cx="13" cy="5" r="3.4"/><circle cx="19" cy="6" r="3"/><path d="M2 17c0-4 3-6 5-6M24 17c0-4-3-6-5-6M7 18c0-4 3-7 6-7s6 3 6 7"/></svg></span><div><h4>Eco Friendly</h4><p>Lorem ipsum dolor sit amet, consectetur adipiscing elit, sed</p></div></div>

<!-- services -->
<h2 class="heading" style="left:0;top:1998px;width:1200px;text-align:center;font-size:48px">Our Services</h2>
<div class="rule" style="left:553px;top:2069px;width:94px"></div>
<article class="svc" style="left:69px">
  <div class="svc-photo" role="img" aria-label="Cleaner spraying and wiping a table" style="background:linear-gradient(135deg,#5f7a4e,#c9b79a)"></div>
  <h3>SERVICE 1</h3>
  <p>Lorem ipsum dolor sit amet, consectetur adipiscing elit, sed do eiusmod tempor incididunt ut labore et dolore magna aliqua. Quis ipsum suspendisse ultrices gravida. Risus commodo viverra maecenas ...</p>
  <div class="btn btn-blue">Read More</div>
</article>
<article class="svc" style="left:429px">
  <div class="svc-photo" role="img" aria-label="Man cleaning a window with spray and cloth" style="background:linear-gradient(135deg,#9fb0b8,#3c3c3c)"></div>
  <h3>SERVICE 2</h3>
  <p>Lorem ipsum dolor sit amet, consectetur adipiscing elit, sed do eiusmod tempor incididunt ut labore et dolore magna aliqua. Quis ipsum suspendisse ultrices gravida. Risus commodo viverra maecenas ...</p>
  <div class="btn btn-blue">Read More</div>
</article>
<article class="svc" style="left:789px">
  <div class="svc-photo" role="img" aria-label="Worker vacuuming an office floor" style="background:linear-gradient(180deg,#c7d2dc,#e6e9ec)"></div>
  <h3>SERVICE 3</h3>
  <p>Lorem ipsum dolor sit amet, consectetur adipiscing elit, sed do eiusmod tempor incididunt ut labore et dolore magna aliqua. Quis ipsum suspendisse ultrices gravida. Risus commodo viverra maecenas ...</p>
  <div class="btn btn-blue">Read More</div>
</article>
<div class="btn btn-red" style="left:500px;top:2667px;width:200px;height:54px;font-size:13px">View All Services</div>

<!-- welcome -->
<section class="welcome" role="img" aria-label="Red-tinted background of a cleaner wiping a mirror"></section>
<p class="welcome-kicker">WELCOME TO</p>
<h2 class="welcome-title">Harbor Tidy Team</h2>
<p class="welcome-copy">Lorem ipsum dolor sit amet, consectetur adipiscing elit, sed do eiusmod tempor incididunt ut labore et dolore magna aliqua.<br>Quis ipsum suspendisse ultrices gravida Risus commodo viverra maecenas accumsan lacus vel facilisis.</p>
<div class="btn" style="left:508px;top:3131px;width:186px;height:46px;background:#fff;color:var(--red);font-size:14px">Contact Us</div>

<!-- contact -->
<h2 class="heading" style="left:72px;top:3404px;font-size:48px">Contact Us</h2>
<div class="rule" style="left:74px;top:3475px;width:52px"></div>
<p class="contact-sub">For more information,Please fill out the following and we will be in touch shortly</p>
<div class="field" style="left:78px;top:3563px;width:260px;height:52px">First Name</div>
<div class="field" style="left:362px;top:3563px;width:260px;height:52px">Second Name</div>
<div class="field" style="left:78px;top:3641px;width:260px;height:52px">Phone</div>
<div class="field" style="left:362px;top:3641px;width:260px;height:52px">Subject</div>
<div class="field" style="left:78px;top:3716px;width:544px;height:101px;padding-top:30px">Message</div>
<div class="btn btn-red" style="left:78px;top:3850px;width:175px;height:45px;font-size:12px">Submit A Message</div>
<div class="ring" style="left:698px;top:3439px;width:432px;height:432px"></div>
<div class="disc" role="img" aria-label="Gloved hand spraying and wiping a stair railing" style="left:722px;top:3463px;width:384px;height:384px;background:radial-gradient(circle at 45% 45%,#8fc8d4,#8a7a6c 70%)"></div>

<!-- footer -->
<footer class="footer" role="img" aria-label="Blue-tinted city skyline"></footer>
<div class="abs" style="left:145px;top:4150px;display:flex;align-items:center;gap:12px"><span class="brand-dot"></span><span class="brand-name" style="color:#fff">HARBOR TIDY TEAM</span></div>
<span class="social" style="left:213px"></span>
<span class="social" style="left:262px"></span>
<span class="social" style="left:308px"></span>

<h3 class="foot-h" style="left:551px;top:4105px">Links</h3>
<div class="foot-rule" style="left:552px;top:4150px"></div>
<ul class="foot-list"><li>About Us</li><li>Our Services</li><li>Testimonials</li><li>Contact</li></ul>

<h3 class="foot-h" style="left:824px;top:4105px">Contact</h3>
<div class="foot-rule" style="left:825px;top:4150px"></div>
<div class="foot-contact" style="top:4175px"><span class="foot-icon"><svg width="16" height="20" viewBox="0 0 16 20"><path d="M8 0a8 8 0 0 0-8 8c0 6 8 12 8 12s8-6 8-12a8 8 0 0 0-8-8z" fill="#e8321e"/><circle cx="8" cy="8" r="3" fill="#fff"/></svg></span><span>Lorem ipsum,Lorem ipsum.<br>Lorem ipsum</span></div>
<div class="foot-contact" style="top:4239px"><span class="foot-icon"><svg width="18" height="18" viewBox="0 0 24 24"><path d="M7 3.5c.8-.5 1.7-.2 2.1.5l1.2 2.4c.4.7.1 1.5-.4 1.9l-1 .8c.8 1.8 2.2 3.2 3.9 4.1l.8-1c.4-.6 1.2-.8 1.9-.4l2.4 1.2c.8.4 1 1.3.5 2.1l-.8 1.3c-.7 1.1-2 1.5-3.2 1.1-4-1.5-7.1-4.6-8.5-8.7-.4-1.2 0-2.5 1.1-3.2z" fill="#e8321e"/></svg></span><span>(555) 201 4870</span></div>
<div class="foot-contact" style="top:4294px"><span class="foot-icon"><svg width="18" height="14" viewBox="0 0 18 14"><rect width="18" height="14" rx="2" fill="#e8321e"/><path d="M1 1l8 7 8-7" fill="none" stroke="#fff" stroke-width="1.5"/></svg></span><span>hello@harbortidyteam.com</span></div>

<div class="abs" style="left:145px;top:4375px;width:910px;height:1px;background:rgba(255,255,255,.3)"></div>
<p class="copyright">Copyright © 2025 All Rights Reserved By Harbor Tidy Team</p>

</body>
</html>
```